design a construction company business card

Design business card around our logo. Card must have all the typical info: name, title, address, phone, email, business name, etc. Somewhere on the card I would like to see our motto "Solid Foundations... Lasting Relationships." Consider adding a splash of bright orange to the card to complement the blues and silvers/grays in the logo. We are open to metallic inks, textures, etc. We would like to see options on both light and dark backgrounds. The font in the logo is Euro Technic Extended Regular.

```html
<!DOCTYPE html>
<html lang="en">
<head>
<meta charset="utf-8">
<title>Harlow Contracting – Business Card</title>
<link rel="stylesheet" href="https://fonts.googleapis.com/css2?family=Roboto:wght@400;500;700&display=swap">
<style>
  :root {
    --page: #f7f7f7;
    --navy: #0e1730;
    --steel: #86888c;
    --brand-blue: #2f6dc4;
    --muted: #8c9097;
    --white: #ffffff;
    --rule: #9a9da3;
  }
  * { box-sizing: border-box; margin: 0; padding: 0; }
  html, body {
    width: 1200px; height: 1000px; overflow: hidden;
    background: var(--page);
    font-family: "Roboto", Arial, sans-serif;
  }
  .card {
    position: absolute;
    background: var(--navy);
    overflow: hidden;
    box-shadow: 0 14px 22px rgba(0,0,0,0.35);
  }
  .card--front { left: 255px; top: 72px; width: 689px; height: 394px; }
  .card--back  { left: 255px; top: 529px; width: 692px; height: 396px; }
  .card__corners { position: absolute; inset: 0; width: 100%; height: 100%; }
  .card__corners path { fill: var(--steel); }

  .wordmark {
    position: absolute;
    color: var(--brand-blue);
    font-weight: 700;
    text-align: center;
    line-height: 1;
  }
  .wordmark__mark {
    display: block; width: 22px; height: 22px;
    background: var(--brand-blue); margin: 0 auto 12px;
  }
  .wordmark__name { display: block; letter-spacing: 3px; }
  .wordmark__suffix { display: block; letter-spacing: 2px; margin-top: 8px; }

  .card--front .wordmark { left: 0; right: 0; top: 150px; }
  .card--front .wordmark__name { font-size: 50px; }
  .card--front .wordmark__suffix { font-size: 18px; }

  .motto {
    position: absolute; left: 0; right: 0; top: 284px;
    text-align: center; color: var(--muted);
    font-size: 17px; line-height: 20px; letter-spacing: 0.3px;
  }

  .card--back .wordmark { right: 47px; top: 46px; width: 216px; }
  .card--back .wordmark__mark { width: 18px; height: 18px; margin-bottom: 10px; }
  .card--back .wordmark__name { font-size: 42px; }
  .card--back .wordmark__suffix { font-size: 14px; margin-top: 7px; }

  .person { position: absolute; right: 47px; top: 185px; text-align: right; }
  .person__name { color: var(--brand-blue); font-size: 27px; font-weight: 500; }
  .person__title { color: var(--white); font-size: 17px; margin-top: 4px; }
  .person__title strong { color: var(--muted); font-weight: 500; }

  .divider {
    position: absolute; left: 42px; top: 226px; width: 338px; height: 2px;
    background: var(--rule);
  }

  .contacts { position: absolute; left: 33px; top: 248px; list-style: none; }
  .contacts li {
    display: flex; align-items: center; gap: 8px;
    color: var(--white); font-size: 17px; height: 28px;
  }
  .contacts svg { width: 19px; height: 19px; fill: var(--muted); flex: none; }

  .address {
    position: absolute; right: 47px; top: 306px;
    text-align: right; color: var(--muted); font-size: 17px; line-height: 25px;
    font-style: normal;
  }
</style>
</head>
<body>

<section class="card card--front">
  <svg class="card__corners" viewBox="0 0 689 394" preserveAspectRatio="none" aria-hidden="true">
    <path d="M0,0 H220 Q70,55 0,190 Z"/>
    <path d="M689,328 Q665,372 613,394 H689 Z"/>
  </svg>
  <div class="wordmark">
    <span class="wordmark__mark"></span>
    <span class="wordmark__name">HARLOW</span>
    <span class="wordmark__suffix">CONTRACTING, INC.</span>
  </div>
  <p class="motto">Solid Foundations... Lasting Relationships</p>
</section>

<section class="card card--back">
  <svg class="card__corners" viewBox="0 0 692 396" preserveAspectRatio="none" aria-hidden="true">
    <path d="M0,0 H220 Q70,55 0,189 Z"/>
    <path d="M692,326 Q668,372 613,396 H692 Z"/>
  </svg>

  <div class="wordmark">
    <span class="wordmark__mark"></span>
    <span class="wordmark__name">HARLOW</span>
    <span class="wordmark__suffix">CONTRACTING, INC.</span>
  </div>

  <div class="person">
    <p class="person__name">Marcus Bell</p>
    <p class="person__title">CEO of <strong>Harlow Contracting, INC</strong></p>
  </div>

  <div class="divider"></div>

  <ul class="contacts">
    <li>
      <svg viewBox="0 0 24 24" aria-hidden="true"><path d="M6.6 10.8a15 15 0 0 0 6.6 6.6l2.2-2.2a1 1 0 0 1 1-.25 11.4 11.4 0 0 0 3.6.57 1 1 0 0 1 1 1V20a1 1 0 0 1-1 1A17 17 0 0 1 3 4a1 1 0 0 1 1-1h3.5a1 1 0 0 1 1 1c0 1.25.2 2.45.57 3.57a1 1 0 0 1-.25 1z"/></svg>
      (02) 5550 1234
    </li>
    <li>
      <svg viewBox="0 0 24 24" aria-hidden="true"><path d="M8 1h8a2 2 0 0 1 2 2v18a2 2 0 0 1-2 2H8a2 2 0 0 1-2-2V3a2 2 0 0 1 2-2zm0 3v14h8V4zm4 15.5a1 1 0 1 0 0 2 1 1 0 0 0 0-2z"/></svg>
      0400 555 012
    </li>
    <li>
      <svg viewBox="0 0 24 24" aria-hidden="true"><path d="M2 5h20v14H2zm2 2v.5l8 5 8-5V7z"/></svg>
      info@harlowbuilds.com
    </li>
    <li>
      <svg viewBox="0 0 24 24" aria-hidden="true"><path d="M12 2a10 10 0 1 0 0 20 10 10 0 0 0 0-20zm-1 17.9A8 8 0 0 1 4.1 11H7v2l4 2zm6.9-2.9A2 2 0 0 0 16 16h-1v-3l-3-1V9h2l2-3h1.2a8 8 0 0 1 .7 11z"/></svg>
      www.harlowbuilds.com
    </li>
  </ul>

  <address class="address">
    118/4 Keel St, Riverton<br>
    NSW 2000, NY
  </address>
</section>

</body>
</html>
```